Stonebrace Business Card Design

The Stonebrace Co is an aggregate (crushing) equipment dealer serving Western Canadian provinces. Stonebrace is a distributor of aggregate equipment for different manufacturers.

We are looking to change and update the existing business card which has been used since the existence of the company. A copy of existing card has been attached for reference. The Stonebrace Co logo we want to remain the same and we want the green color to remain the same.

We are wanting something new with a different look. A refreshing card to show a new modern and updated look. No longer wanting to have the manufacturers on the back of the card but something more like our logo on the back of the card with a statement like "Crushing Solutions"

ideas could be:
- card can be different colors on front and back
- front or reverse of the card could possibly be the green color with the logo in black

Target Market(s)

Owners of Aggregate/Crushing companies

Contact Information for Business Card

see above

Requirements
Must have
• - logo to remain same along with same font within logo
• - green color to remain same
Nice to have
• as noted above under project description
Should not have

```html
<!DOCTYPE html>
<html lang="en">
<head>
<meta charset="utf-8">
<title>Stonebrace Co – Business Card</title>
<link rel="stylesheet" href="https://fonts.googleapis.com/css2?family=Roboto:wght@400;700&family=Roboto+Condensed:wght@700&display=swap">
<style>
  :root {
    --brand-green: #8a8d0c;
    --card-white: #efefef;
    --ink-dark: #231f20;
    --text-light: #ffffff;
    --canvas-bg: #e6e3de;
  }
  * { margin: 0; padding: 0; box-sizing: border-box; }
  html, body {
    width: 1200px; height: 960px; overflow: hidden;
    background: var(--canvas-bg);
    font-family: "Roboto", Arial, sans-serif;
  }
  .canvas { position: relative; width: 1200px; height: 960px; }

  .card {
    position: absolute;
    left: 320px;
    width: 600px;
    height: 342px;
    border-radius: 16px;
    overflow: hidden;
  }

  /* Reverse side */
  .card-back { top: 108px; background: var(--brand-green); }
  .card-back .brand-name {
    position: absolute; left: 0; right: 0; top: 142px;
    text-align: center;
    font-weight: 700; font-size: 34px; letter-spacing: 0.5px;
    color: var(--ink-dark);
  }
  .card-back .tagline {
    position: absolute; left: 0; right: 0; top: 290px;
    text-align: center;
    font-weight: 700; font-size: 15px;
    color: var(--ink-dark);
  }

  /* Front side */
  .card-front { top: 493px; background: var(--brand-green); }
  .front-panel {
    position: absolute; left: 440px; top: 0; width: 160px; height: 100%;
    background: var(--card-white);
  }
  .front-oval {
    position: absolute; left: 228px; top: -40px;
    width: 440px; height: 422px;
    border-radius: 50%;
    background: var(--card-white);
  }
  .brand-mark {
    position: absolute; left: 380px; top: 105px;
    width: 80px; height: 80px; border-radius: 50%;
    background: var(--brand-green);
  }
  .card-front .brand-name {
    position: absolute; left: 240px; width: 360px; top: 215px;
    text-align: center;
    font-weight: 700; font-size: 22px;
    color: var(--ink-dark);
  }

  .contact {
    position: absolute; left: 34px; top: 74px;
    color: var(--text-light);
    font-size: 14px; line-height: 18px;
  }
  .contact .person-name {
    font-family: "Roboto Condensed", "Arial Narrow", sans-serif;
    font-weight: 700; font-size: 21px; line-height: 24px;
  }
  .contact .person-title { font-size: 14px; margin-bottom: 9px; }
  .contact .address { margin-bottom: 10px; }
  .contact-list { list-style: none; }
  .contact-list li {
    display: flex; align-items: center; gap: 9px;
    height: 19px;
  }
  .contact-list svg { width: 14px; height: 14px; fill: var(--text-light); flex: none; }
</style>
</head>
<body>
<main class="canvas">

  <section class="card card-back" aria-label="Card reverse">
    <p class="brand-name">THE STONEBRACE CO.</p>
    <p class="tagline">Crushing Solutions</p>
  </section>

  <section class="card card-front" aria-label="Card front">
    <div class="front-panel"></div>
    <div class="front-oval"></div>
    <div class="brand-mark"></div>
    <p class="brand-name">THE STONEBRACE CO.</p>

    <div class="contact">
      <p class="person-name">DALE MARSH</p>
      <p class="person-title">CEO/FOUNDER</p>
      <p class="address">2210- 48B Avenue<br>Nisku, Alberta T9E 2K1</p>
      <ul class="contact-list">
        <li>
          <svg viewBox="0 0 14 14" aria-hidden="true"><path d="M3 1l2.5 3-1.3 1.5c.8 1.7 2.2 3.1 3.9 3.9L9.6 8.1 12.6 10.6 11 13C5.8 12.5 1.5 8.2 1 3z"/></svg>
          <span>780.555.0142</span>
        </li>
        <li>
          <svg viewBox="0 0 14 14" aria-hidden="true"><path d="M4 0h6a1 1 0 0 1 1 1v12a1 1 0 0 1-1 1H4a1 1 0 0 1-1-1V1a1 1 0 0 1 1-1zm.5 1.5v9h5v-9zM7 11.5a.8.8 0 1 0 0 1.6.8.8 0 0 0 0-1.6z"/></svg>
          <span>780.555.0187</span>
        </li>
        <li>
          <svg viewBox="0 0 14 14" aria-hidden="true"><path d="M3 1h7l1 1v3H3zM1 6h12v5h-2v2H3v-2H1zm3 4v2h6v-2z"/></svg>
          <span>780.555.0163</span>
        </li>
        <li>
          <svg viewBox="0 0 14 14" aria-hidden="true"><path d="M1 3h12v8H1zm1 1.2v.4l5 3.2 5-3.2v-.4z"/></svg>
          <span>dale@stonebrace.com</span>
        </li>
        <li>
          <svg viewBox="0 0 14 14" aria-hidden="true"><path d="M7 1a6 6 0 1 0 0 12A6 6 0 0 0 7 1zm-1 2.5l2 1-1 2 2 1v2.5l-2 1.5-1-2.5-2-1V5z"/></svg>
          <span>www.stonebrace.ca</span>
        </li>
      </ul>
    </div>
  </section>

</main>
</body>
</html>
```